Summit Builders Web Site / Business Cards

Construction Company that specializes in Water and Fire Damage, Residential ReModels, Landscaping and Building ADU (Accessory Dwelling Unit)

Growing and changing families often need additional space, and a remodeling project can often provide that. Adding a new area, or repurposing an existing one can satisfy this requirement.

Other times, homeowners want to update the look in their kitchen or bathroom with more than just a change of cabinetry or vanity doors and drawers. Whatever your needs are, Summit Builders has skilled workers who are bonded and insured, and ready to make your dreams and visions a reality.

Target Market(s)

Home Owners

Industry/Entity Type

Construction Company

Contact Information for Business Card

Center Logo with our information on the corners

Back side to be Logo Only
Contact Info
CSLB License # 2418596
info@summitbuildersca.example
www.summitbuildersca.example

Coding

Coded - Design and coding required

Number of Pages Required

5+ page

Font styles to use
Serif
Sans Serif

Requirements
Must have
• Using our Logo Colors
Home
About Us
Services
Projects / Portfolio
Contact Us
Nice to have
• Colors matching our Logo
Should not have
• Black because it doesnt match our logo

```html
<!DOCTYPE html>
<html lang="en">
<head>
<meta charset="utf-8">
<title>Summit Builders</title>
<link href="https://fonts.googleapis.com/css2?family=Poppins:wght@400;500;600;700;800&family=Open+Sans:wght@400;600&display=swap" rel="stylesheet">
<style>
:root{
  --orange:#f26f21;
  --orange-dark:#d85b12;
  --ink:#2b2b2b;
  --text:#6b6b6b;
  --muted:#9a9a9a;
  --light:#f3f3f3;
  --gray:#ececec;
  --white:#ffffff;
  --footer-bar:#3a3a3a;
}
*{box-sizing:border-box;margin:0;padding:0}
html,body{width:1200px;height:5312px;overflow:hidden}
body{font-family:"Open Sans",Arial,sans-serif;color:var(--text);background:var(--white);position:relative}
h1,h2,h3,h4,.brand,.btn,.nav a{font-family:"Poppins",Arial,sans-serif}
.abs{position:absolute}
.photo{position:absolute}

/* top bar */
.topbar{position:absolute;top:0;left:0;width:1200px;height:48px;background:var(--light);font-size:13px;display:flex;align-items:center;justify-content:space-between;padding:0 88px}
.topbar .addr{display:flex;align-items:center;gap:8px}
.topbar .right{display:flex;align-items:center;gap:16px}
.topbar .phone{color:var(--orange);font-weight:600}
.social{display:flex;gap:10px}
.social span{width:14px;height:14px;border-radius:3px;background:var(--muted);display:block}

/* header */
.header{position:absolute;top:48px;left:0;width:1200px;height:132px;display:flex;align-items:center;justify-content:space-between;padding:0 88px}
.header .lab{color:var(--orange);font-size:13px}
.header .val{color:var(--ink);font-size:15px;font-weight:600}
.header .right{text-align:right}
.brand{display:flex;align-items:center;gap:12px;color:var(--ink);font-weight:700;font-size:26px;letter-spacing:1px;text-transform:uppercase}
.brand i{width:34px;height:34px;background:var(--orange);display:block}

/* hero */
.hero{top:180px;left:0;width:1200px;height:652px;background:linear-gradient(135deg,#8a7d6e 0%,#5e5347 45%,#a89684 100%)}
.hero::after{content:"";position:absolute;inset:0;background:rgba(20,20,20,.45)}
.nav{position:absolute;top:180px;left:88px;width:1024px;height:64px;display:flex;z-index:2}
.nav .links{flex:1;background:var(--orange);display:flex;align-items:center;gap:40px;padding-left:36px}
.nav a{color:var(--white);text-decoration:none;font-size:15px;font-weight:500}
.nav .nav-quote{width:172px;height:64px;background:var(--white);color:var(--orange);font-family:"Poppins",sans-serif;font-weight:600;display:flex;align-items:center;justify-content:center;font-size:15px}
.hero-text{position:absolute;top:420px;left:0;width:1200px;text-align:center;color:var(--white);z-index:2}
.hero-text .kicker{font-family:"Poppins",sans-serif;font-size:22px;letter-spacing:1px}
.hero-text h1{font-size:60px;font-weight:700;margin-top:6px}
.hero-text h1 span{color:var(--orange)}
.hero-text p{font-size:16px;line-height:26px;width:600px;margin:14px auto 0}
.hero-btns{display:flex;justify-content:center;gap:24px;margin-top:40px}
.btn{display:inline-flex;align-items:center;justify-content:center;height:48px;padding:0 30px;font-size:14px;font-weight:600;text-transform:uppercase}
.btn-ghost{border:2px solid var(--white);color:var(--white)}
.btn-solid{background:var(--orange);color:var(--white)}

/* services */
.services{top:832px;left:0;width:1200px;height:1108px;background:var(--white)}
.mark{position:absolute;top:100px;left:580px;width:40px;height:40px;background:var(--orange)}
.sec-title{position:absolute;left:0;width:1200px;text-align:center}
.services h2{top:190px;font-size:26px;font-weight:700;color:var(--ink);line-height:34px;text-transform:uppercase}
.services .sub{top:268px;font-family:"Poppins",sans-serif;font-size:32px;font-weight:700;color:var(--orange)}
.card{position:absolute;width:324px;height:312px;background:var(--white);box-shadow:0 4px 24px rgba(0,0,0,.1);text-align:center;padding-top:28px}
.card .ico{width:76px;height:76px;margin:0 auto;border-radius:50%;background:var(--light);display:flex;align-items:center;justify-content:center}
.card h3{font-size:18px;font-weight:600;color:var(--ink);margin-top:18px}
.card p{font-size:13px;line-height:20px;width:230px;margin:12px auto 0}
.card .more{margin-top:18px;display:flex;justify-content:center;align-items:center;gap:8px;font-size:13px;font-weight:600;color:var(--ink)}
.dot{width:12px;height:12px;border-radius:50%;background:var(--orange);display:inline-block}

/* about */
.about{top:1940px;left:0;width:1200px;height:760px;background:var(--gray)}
.about .kicker{position:absolute;top:100px;left:620px;color:var(--orange);font-size:14px;font-family:"Poppins",sans-serif}
.about h2{position:absolute;top:128px;left:620px;font-size:40px;line-height:50px;font-weight:700;color:var(--ink);text-transform:uppercase}
.about h2 span{color:var(--orange)}
.about p{position:absolute;top:246px;left:620px;width:500px;font-size:14px;line-height:24px}
.feat{position:absolute;width:240px;display:flex;align-items:center;gap:14px;font-family:"Poppins",sans-serif;font-size:13px;font-weight:600;color:var(--ink);text-transform:uppercase}
.feat .c{width:48px;height:48px;border-radius:50%;background:var(--orange);flex:none;display:flex;align-items:center;justify-content:center}

/* projects */
.projects{top:2700px;left:0;width:1200px;height:1040px}
.projects .kicker{top:70px;color:var(--orange);font-size:14px;font-family:"Poppins",sans-serif;text-transform:uppercase}
.projects h2{top:98px;font-size:40px;font-weight:700;color:var(--ink)}
.proj{position:absolute;width:324px;height:320px;background:var(--white);box-shadow:0 4px 24px rgba(0,0,0,.1)}
.proj .ph{position:absolute;top:0;left:0;width:324px;height:240px}
.proj .tag{position:absolute;top:224px;left:0;background:var(--orange);color:var(--white);font-size:11px;padding:6px 14px;text-transform:uppercase}
.proj h3{position:absolute;top:272px;left:14px;font-size:16px;font-weight:600;color:var(--ink);text-transform:uppercase}
.btn-outline{position:absolute;top:952px;left:496px;width:208px;height:44px;border:2px solid var(--orange);color:var(--orange);font-size:13px}

/* stats */
.stats{top:3740px;left:88px;width:1024px;height:140px;display:flex;justify-content:space-around;align-items:center;text-align:center}
.stats b{display:block;font-family:"Poppins",sans-serif;font-size:46px;font-weight:600;color:var(--orange);line-height:54px}
.stats small{font-size:14px;color:var(--ink);text-transform:uppercase}

/* testimonials */
.testi{top:3880px;left:0;width:1200px;height:660px;background:linear-gradient(180deg,#d9d9d9 0%,#bdbdbd 50%,#cfcfcf 100%)}
.testi .kicker{top:64px;color:var(--orange);font-size:14px;font-family:"Poppins",sans-serif;text-transform:uppercase}
.testi h2{top:94px;font-size:40px;font-weight:700;color:var(--ink)}
.review{position:absolute;top:200px;width:492px;height:250px;background:var(--white);padding:36px 40px}
.review p{font-size:14px;line-height:22px;width:340px}
.review .qm{position:absolute;top:20px;font-family:"Poppins",sans-serif;font-size:80px;line-height:80px;color:var(--orange);font-weight:700}
.review .who{position:absolute;top:156px;left:40px;display:flex;align-items:center;gap:18px}
.avatar{width:76px;height:76px;border-radius:50%;background:linear-gradient(135deg,#c7a58c,#8e6f5c);border:3px solid var(--orange)}
.who b{display:block;color:var(--orange);font-family:"Poppins",sans-serif;font-size:17px;font-weight:600}
.who span{font-size:13px}
.pager{position:absolute;top:588px;left:492px;display:flex;gap:8px}
.pager i{width:48px;height:4px;background:var(--ink);display:block}
.pager i:first-child{background:var(--orange)}

/* cta */
.cta-photo{top:4600px;left:88px;width:470px;height:200px;background:linear-gradient(160deg,#f4a35f 0%,#e17a33 40%,#6d6a66 100%)}
.cta{position:absolute;top:4612px;left:544px;width:568px;height:176px;background:var(--orange);padding:28px 36px;color:var(--white)}
.cta h2{font-size:27px;line-height:36px;font-weight:700}
.cta .btn{height:40px;border:2px solid var(--white);color:var(--white);margin-top:16px;font-size:12px;padding:0 22px}

/* footer */
.footer{top:4820px;left:0;width:1200px;height:420px}
.footer .col{position:absolute;top:40px}
.footer h4{font-size:22px;font-weight:500;color:var(--ink);margin-bottom:22px}
.footer p,.footer li{font-size:13px;line-height:22px}
.footer ul{list-style:none}
.footer li{display:flex;align-items:center;gap:10px;margin-bottom:12px;color:var(--ink)}
.footer li::before{content:"";width:12px;height:1px;background:var(--orange)}
.footer .hours b{color:var(--orange);font-weight:600}
.footer .contact span{color:var(--orange)}
.bottom{position:absolute;top:5240px;left:0;width:1200px;height:72px;background:var(--footer-bar);display:flex;justify-content:space-between;align-items:center;padding:0 88px;color:#cfcfcf;font-size:13px}
.bottom .social span{background:#cfcfcf}
</style>
</head>
<body>

<div class="topbar">
  <div class="addr">
    <svg width="12" height="14" viewBox="0 0 12 14"><path d="M6 0a5 5 0 0 0-5 5c0 4 5 9 5 9s5-5 5-9a5 5 0 0 0-5-5zm0 7a2 2 0 1 1 0-4 2 2 0 0 1 0 4z" fill="#f26f21"/></svg>
    4820 Ridgeview Ave, Santa Ana, CA 92704
  </div>
  <div class="right">
    <span class="phone">(714) 555-0148</span>
    <div class="social"><span></span><span></span><span></span><span></span><span></span></div>
  </div>
</div>

<header class="header">
  <div><div class="lab">Call us</div><div class="val">+1 714 555 0192</div></div>
  <div class="brand"><i></i>Summit Builders</div>
  <div class="right"><div class="lab">Email us now</div><div class="val">info@summitbuildersca.example</div></div>
</header>

<section class="photo hero" role="img" aria-label="Construction workers measuring and cutting timber on a building site"></section>
<nav class="nav">
  <div class="links"><a>About Us</a><a>Services</a><a>Projects</a><a>Contact Us</a></div>
  <div class="nav-quote">GET A QUOTE &#8250;</div>
</nav>
<div class="hero-text">
  <div class="kicker">WE ARE PROFESSIONAL</div>
  <h1>The Best <span>Choose</span> us</h1>
  <p>Our Company has consistently embraced innovation to provide a superior level of true excellence for our customers.</p>
  <div class="hero-btns"><span class="btn btn-ghost">View More</span><span class="btn btn-solid">Get a Quote</span></div>
</div>

<section class="abs services">
  <div class="mark"></div>
  <h2 class="sec-title">Technology to take products from<br>an idea all the way to the end consumer.</h2>
  <div class="sec-title sub">WHAT WE DO</div>

  <div class="card" style="top:336px;left:88px">
    <div class="ico"><svg width="40" height="40" viewBox="0 0 40 40" fill="none" stroke="#f26f21" stroke-width="2.5"><path d="M5 19L20 6l15 13M9 16v17h22V16M16 33V23h8v10"/></svg></div>
    <h3>Home Construction</h3>
    <p>We build new homes from the ground up with skilled crews, quality materials and careful planning.</p>
    <div class="more"><span class="dot"></span>Read More</div>
  </div>
  <div class="card" style="top:336px;left:438px">
    <div class="ico"><svg width="40" height="40" viewBox="0 0 40 40" fill="none" stroke="#f26f21" stroke-width="2.5"><rect x="8" y="6" width="24" height="10"/><path d="M20 16v6M17 22h6v12h-6z"/></svg></div>
    <h3>Exterior Design</h3>
    <p>Fresh facades, siding, paint and landscaping that give your home lasting curb appeal and value.</p>
    <div class="more"><span class="dot"></span>Read More</div>
  </div>
  <div class="card" style="top:336px;left:788px">
    <div class="ico"><svg width="40" height="40" viewBox="0 0 40 40" fill="none" stroke="#f26f21" stroke-width="2.5"><rect x="6" y="14" width="16" height="20"/><rect x="22" y="6" width="12" height="28"/><path d="M10 20h8M10 26h8M26 12h4M26 18h4M26 24h4"/></svg></div>
    <h3>Building Remodeling</h3>
    <p>Repurpose existing rooms or add new space to fit the needs of a growing and changing family.</p>
    <div class="more"><span class="dot"></span>Read More</div>
  </div>
  <div class="card" style="top:688px;left:88px">
    <div class="ico"><svg width="40" height="40" viewBox="0 0 40 40" fill="none" stroke="#f26f21" stroke-width="2.5"><path d="M4 32h32M6 32V24h12v8M18 24V16h12v16M10 16h8v8"/></svg></div>
    <h3>Renovation</h3>
    <p>Water and fire damage repairs handled quickly so your home is safe, sound and restored again.</p>
    <div class="more"><span class="dot"></span>Read More</div>
  </div>
  <div class="card" style="top:688px;left:438px">
    <div class="ico"><svg width="40" height="40" viewBox="0 0 40 40" fill="none" stroke="#f26f21" stroke-width="2.5"><path d="M26 6l8 8-14 14-8-8zM12 20l-6 14 14-6"/></svg></div>
    <h3>Interior Design</h3>
    <p>Updated kitchens and bathrooms with more than new doors, from layout to finishes and fixtures.</p>
    <div class="more"><span class="dot"></span>Read More</div>
  </div>
  <div class="card" style="top:688px;left:788px">
    <div class="ico"><svg width="40" height="40" viewBox="0 0 40 40" fill="none" stroke="#f26f21" stroke-width="2.5"><path d="M6 28a14 14 0 0 1 28 0zM4 28h32v4H4zM20 14V8"/></svg></div>
    <h3>Safety Management</h3>
    <p>Bonded and insured workers follow strict site safety practices on every project we complete.</p>
    <div class="more"><span class="dot"></span>Read More</div>
  </div>
</section>

<section class="abs about">
  <div class="photo" style="top:100px;left:88px;width:336px;height:320px;background:linear-gradient(135deg,#7fa7c9,#c9b48a)" role="img" aria-label="Site engineers in hard hats reviewing a new building"></div>
  <div class="photo" style="top:230px;left:340px;width:200px;height:430px;background:linear-gradient(180deg,#4d7fb0,#9ec1de)" role="img" aria-label="Modern glass office tower seen from below"></div>
  <div class="photo" style="top:440px;left:88px;width:232px;height:220px;background:linear-gradient(135deg,#b9b2a6,#6e6a63)" role="img" aria-label="Worker on scaffolding at a construction site"></div>
  <div class="kicker">WHO WE ARE</div>
  <h2>We <span>Deliver</span><br>Landmark <span>Projects</span></h2>
  <p>Our skilled team plans and builds homes, additions and ADUs with care, from the first sketch to the final walkthrough, keeping you informed and your project on schedule and on budget.</p>
  <div class="feat" style="top:376px;left:620px"><span class="c"><svg width="22" height="22" viewBox="0 0 22 22" fill="none" stroke="#fff" stroke-width="2"><circle cx="11" cy="8" r="5"/><path d="M7 12l-2 8 6-3 6 3-2-8"/></svg></span>We're reputed for excellence</div>
  <div class="feat" style="top:376px;left:880px"><span class="c"><svg width="22" height="22" viewBox="0 0 22 22" fill="none" stroke="#fff" stroke-width="2"><path d="M2 11l5-5 4 4 4-4 5 5-9 8z"/></svg></span>We build partnerships</div>
  <div class="feat" style="top:466px;left:620px"><span class="c"><svg width="22" height="22" viewBox="0 0 22 22" fill="none" stroke="#fff" stroke-width="2"><path d="M11 2l8 3v6c0 5-4 8-8 9-4-1-8-4-8-9V5z"/></svg></span>Guided by commitment</div>
  <div class="feat" style="top:466px;left:880px"><span class="c"><svg width="22" height="22" viewBox="0 0 22 22" fill="none" stroke="#fff" stroke-width="2"><circle cx="8" cy="7" r="3"/><circle cx="15" cy="7" r="3"/><path d="M2 19c0-4 3-6 6-6s6 2 6 6M14 13c3 0 6 2 6 6"/></svg></span>A team of professionals</div>
</section>

<section class="abs projects">
  <div class="sec-title kicker">Our Industries Work</div>
  <h2 class="sec-title">OUR PROJECTS</h2>

  <div class="proj" style="top:180px;left:88px"><div class="ph" role="img" aria-label="Workers framing a building on site" style="background:linear-gradient(135deg,#d9b07a,#8c6a45)"></div><span class="tag">Construction</span><h3>Building &amp; Construction</h3></div>
  <div class="proj" style="top:180px;left:438px"><div class="ph" role="img" aria-label="Yellow hard hat and house plans" style="background:linear-gradient(135deg,#f2c230,#b7895a)"></div><span class="tag">Fixing</span><h3>Home Fixing &amp; Support</h3></div>
  <div class="proj" style="top:180px;left:788px"><div class="ph" role="img" aria-label="Renovated two-storey family house" style="background:linear-gradient(135deg,#7fa7cf,#a06b55)"></div><span class="tag">Renovation</span><h3>Renovation &amp; Fixing</h3></div>
  <div class="proj" style="top:548px;left:88px"><div class="ph" role="img" aria-label="Large house at dusk with lit windows" style="background:linear-gradient(135deg,#5b6c8f,#d7a06a)"></div><span class="tag">Building</span><h3>Building a Sports City</h3></div>
  <div class="proj" style="top:548px;left:438px"><div class="ph" role="img" aria-label="Modern kitchen with wood cabinets" style="background:linear-gradient(135deg,#8a6b52,#d8cfc2)"></div><span class="tag">Kitchen Design</span><h3>Home &amp; Kitchen Design</h3></div>
  <div class="proj" style="top:548px;left:788px"><div class="ph" role="img" aria-label="Bright living room interior" style="background:linear-gradient(135deg,#e9e4dc,#9a8f82)"></div><span class="tag">Interior</span><h3>Official Interior Design</h3></div>

  <span class="btn btn-outline">View All Projects</span>
</section>

<section class="abs stats">
  <div><b>53</b><small>Total Projects</small></div>
  <div><b>371</b><small>Staff Members</small></div>
  <div><b>15</b><small>Working in States</small></div>
  <div><b>2,600</b><small>Hours for Work</small></div>
</section>

<section class="photo testi" role="img" aria-label="Faded photo of a contractor reviewing plans on site">
  <div class="sec-title kicker">Testimonials</div>
  <h2 class="sec-title">WHAT OUR CLIENTS SAY</h2>
  <div class="review" style="left:88px">
    <span class="qm" style="right:40px">&#8221;</span>
    <p>...and for all the wonderful work you and your crew are doing. Our team has nothing but good things to say, we are really fortunate to have found you for this project.</p>
    <div class="who"><span class="avatar"></span><div><b>Daniel Brooks</b><span>Chairman Oakline</span></div></div>
  </div>
  <div class="review" style="left:620px">
    <span class="qm" style="right:40px">&#8221;</span>
    <p>SummitBuilders is one of the best general contractors we've worked with. The entire team routinely delivered a project of exceptional quality while staying on schedule and under budget.</p>
    <div class="who"><span class="avatar"></span><div><b>Laura Whitfield</b><span>Project Manager</span></div></div>
  </div>
  <div class="pager"><i></i><i></i><i></i><i></i></div>
</section>

<div class="photo cta-photo" role="img" aria-label="Construction site with cranes at sunset"></div>
<div class="cta">
  <h2>SummitBuilders is one of the best general contractors</h2>
  <span class="btn">Book a Consultation</span>
</div>

<footer class="abs footer">
  <div class="col" style="left:88px;width:300px">
    <div class="brand" style="font-size:22px;margin-bottom:22px"><i style="width:28px;height:28px"></i>Summit Builders</div>
    <p>We work 7 days a week, every day excluding major holidays. Contact us if you have an emergency, with our Hotline and Contact form.</p>
    <p class="hours" style="margin-top:14px"><b>Monday - Friday:</b> 10:00 - 18:00<br><b>Saturday:</b> 12:00 - 13:00<br><b>Sunday and holidays:</b> 09:00 - 12:00</p>
  </div>
  <div class="col" style="left:440px;width:320px">
    <h4>Useful Links</h4>
    <div style="display:flex;gap:60px">
      <ul><li>Home</li><li>Company</li><li>Projects</li><li>Contact</li></ul>
      <ul><li>Get a Quote</li><li>Testimonials</li><li>Construction Products</li><li>Privacy Policy</li><li>Terms &amp; Conditions</li></ul>
    </div>
  </div>
  <div class="col contact" style="left:830px;width:290px">
    <h4>Contact Us</h4>
    <p><span>Marcus Hale</span> | Branch Manager</p>
    <p style="margin-top:12px"><span>Office:</span> 714-555-0148<br><span>Direct:</span> 714-555-0163<br><span>Fax:</span> 714-555-0171<br><span>Email:</span> info@summitbuildersca.example</p>
    <p style="margin-top:12px"><span>Address:</span> 4820 Ridgeview Ave<br>Santa Ana, CA 92704</p>
  </div>
</footer>

<div class="bottom">
  <span>Copyright &copy; 2020 All Rights Reserved</span>
  <div class="social"><span></span><span></span><span></span><span></span><span></span></div>
</div>

</body>
</html>
```